banner for website

I need a new banner for my website. My website now is. www.brightmeadowkitchen.com, but I'm changing it to Bright Meadow Table and I need a new banner. I want me to be who it's about. I am my brand. I'm Carla Whitford. So, my name needs to be prominent in the banner along with my photo, which I'm attaching. I want my photo very prominent in the banner and very large. I am attaching my two favorites.
I need the banner plain ( with out the newsletter sign up optin part), so I can use it on my newsletters, emails and letter head, as well. I would like it to be inviting. I I have a certain color scheme I use. Deep dark brown letters with blues and greens. Very earthy and psychologically grounded. I would like to keep that color scheme. In my website banner, I need a opt in to sign up for my free monthly newsletter and receive my Free Pantry Basket Planner.

I want the shopping guide to be small and pleasant looking and to say: "Sign up to receive your Free Pantry Basket Planner and monthly newsletter."

I only want my banner to say: "Bright Meadow Table" "Carla Whitford"

I would also like to have part of the banner without the sign in for the newsletter part off of it. And also one with only the "Bright Meadow Table" and one with "Bright Meadow Table" and "Carla Whitford" without the newsletter sign up part on it either.

I hope you can do this for me. I look forward to seeing your design! Sincerely, Carla
Updates

Project Deadline Extended Reason: I couldn't view the designs so I couldn't look at the ones submitted. I just now got into the website with your company's help. I don't want to be penalized because of a problem with the log in at your site. That was not my fault. Please let me know your thoughts. Added Monday, May 9, 2016

Target Market(s)

people over 40 who have bad health or who want to learn how to be a vegetarian for better health.

Number of Pages Required

1 page

Requirements
Must have
• I want the shopping guide to be small and pleasant looking and to say: "Sign up to receive your Free Pantry Basket Planner and monthly newsletter." I would like it to blend and be elegant and not in the middle of the banner or across my face.
• I only want my banner to say: "Bright Meadow Table" "Carla Whitford"
• I would also like to have part of the banner without the sign in for the newsletter part off of it. And also one with only the "Bright Meadow Table" and one with "Bright Meadow Table" and "Carla Whitford" without the newsletter sign up part on it either.
Nice to have
• Nice font and colors. I want the background to be plants and earthy and inviting.
Should not have
• I updated and added two new photos. I think the one you were using with me in the red top looked funny under my eyes. it was too pink or something. I uploaded a better version of that photo. in hopes that it looks better. Please switch those out if you are using the one with me in the red top.

```html
<!DOCTYPE html>
<html lang="en">
<head>
<meta charset="utf-8">
<title>Bright Meadow Table – Carla Whitford</title>
<link rel="stylesheet" href="https://fonts.googleapis.com/css2?family=Bebas+Neue&family=Didact+Gothic&family=Great+Vibes&family=Merriweather:wght@300&family=Noto+Sans&family=Noto+Serif:ital,wght@0,400;0,700;1,400&family=Roboto:wght@400;700&display=swap">
<style>
  :root {
    --leaf-lime: #4fd62a;
    --leaf-green: #1e9a3a;
    --leaf-cyan: #27d3d0;
    --leaf-teal: #0f7f86;
    --ink-dark: #2a2a2a;
    --logo-ink: #1d3f44;
    --headline-yellow: #f3e21b;
    --bark: #4a3e31;
    --nav-text: #ffffff;
    --home-orange: #e0701e;
    --title-grey: #555555;
    --body-grey: #444444;
    --link-green: #3f7d18;
    --button-green: #1f8f16;
    --button-green-dark: #0f6a0c;
    --paper: #ffffff;
  }

  * { box-sizing: border-box; margin: 0; padding: 0; }

  html, body {
    width: 1200px;
    height: 556px;
    overflow: hidden;
    background: var(--paper);
  }

  .page {
    position: relative;
    width: 1200px;
    height: 556px;
    overflow: hidden;
  }

  /* ---------- Header ---------- */
  .masthead {
    position: absolute;
    left: 0; top: 0;
    width: 1200px;
    height: 240px;
    background:
      radial-gradient(ellipse 260px 200px at 150px 220px, rgba(79,214,42,.85), transparent 70%),
      radial-gradient(ellipse 300px 220px at 1050px 60px, rgba(15,127,134,.7), transparent 70%),
      linear-gradient(100deg, #7fe6d8 0%, var(--leaf-cyan) 22%, var(--leaf-lime) 45%, var(--leaf-green) 62%, var(--leaf-teal) 80%, #6fe0df 100%);
  }

  .portrait {
    position: absolute;
    left: 376px; top: 0;
    width: 320px;
    height: 240px;
    background:
      radial-gradient(ellipse 90px 110px at 170px 110px, #f2cfb4, transparent 75%),
      radial-gradient(ellipse 170px 200px at 160px 140px, #d9b98a, transparent 80%),
      linear-gradient(90deg, rgba(120,200,120,0) 0%, #b9d8a0 25%, #cfe3c0 75%, rgba(120,200,120,0) 100%);
  }

  .brand {
    position: absolute;
    left: 140px; top: 40px;
    display: flex;
    align-items: center;
    gap: 8px;
  }

  .brand-dot {
    width: 46px; height: 46px;
    border-radius: 50%;
    background: var(--leaf-green);
  }

  .brand-name {
    font-family: "Didact Gothic", sans-serif;
    font-size: 27px;
    line-height: 26px;
    color: var(--logo-ink);
  }

  .signature {
    position: absolute;
    left: 184px; top: 124px;
    font-family: "Great Vibes", cursive;
    font-size: 56px;
    color: var(--ink-dark);
    white-space: nowrap;
  }

  .optin {
    position: absolute;
    left: 702px; top: 38px;
    width: 380px;
  }

  .optin-lead {
    font-family: "Roboto", sans-serif;
    font-weight: 700;
    font-size: 16px;
    line-height: 17px;
    color: var(--headline-yellow);
    margin-left: 3px;
  }

  .optin-offer {
    margin-top: 10px;
    font-family: "Bebas Neue", sans-serif;
    font-size: 25px;
    line-height: 24px;
    color: var(--paper);
    letter-spacing: .2px;
  }

  .optin-form {
    margin-top: 14px;
    display: grid;
    grid-template-columns: 179px 179px;
    column-gap: 8px;
    row-gap: 12px;
  }

  .field, .signup-button {
    height: 28px;
    border-radius: 14px;
    font-family: "Roboto", sans-serif;
  }

  .field {
    border: none;
    background: var(--paper);
    padding-left: 18px;
    font-size: 12px;
    color: #8a8a8a;
    display: flex;
    align-items: center;
  }

  .signup-button {
    border: 2px solid var(--paper);
    background: linear-gradient(180deg, #3ab52a 0%, var(--button-green) 50%, var(--button-green-dark) 100%);
    color: var(--paper);
    font-weight: 700;
    font-size: 15px;
    display: flex;
    align-items: center;
    justify-content: center;
  }

  /* ---------- Navigation ---------- */
  .main-nav {
    position: absolute;
    left: 0; top: 240px;
    width: 1200px;
    height: 52px;
    background: var(--bark);
    box-shadow: 0 4px 10px rgba(0,0,0,.25);
    display: flex;
    align-items: flex-end;
    padding-left: 139px;
  }

  .nav-item {
    height: 48px;
    display: flex;
    align-items: center;
    padding: 0 13px;
    font-family: "Noto Serif", serif;
    font-size: 14px;
    color: var(--nav-text);
    white-space: nowrap;
  }

  .nav-item.is-current {
    background: var(--paper);
    color: var(--home-orange);
    border-radius: 3px 3px 0 0;
    padding: 0 11px;
    margin-right: 0;
  }

  /* ---------- Feature cards ---------- */
  .features {
    position: absolute;
    left: 149px; top: 334px;
    display: flex;
    gap: 0;
  }

  .feature {
    width: 320px;
    display: flex;
    gap: 25px;
  }

  .feature-image {
    flex: 0 0 100px;
    height: 100px;
  }

  .feature-image.speaker {
    background: linear-gradient(180deg, #c9c9c9 0%, #a9a6a4 60%, #7d7a78 100%);
  }

  .feature-image.counseling {
    margin-top: 2px;
    width: 92px;
    height: 84px;
    border: 5px solid var(--paper);
    box-shadow: 0 2px 6px rgba(0,0,0,.35);
    transform: rotate(-2deg);
    background: linear-gradient(135deg, #e3b7c9 0%, #c98aa6 45%, #8d6b63 100%);
  }

  .feature-image.products {
    background: linear-gradient(160deg, #1b2b18 0%, #5f8f4a 45%, #c9a36a 100%);
    border-radius: 2px;
  }

  .feature-text { width: 180px; }

  .feature-title {
    font-family: "Merriweather", serif;
    font-weight: 300;
    font-size: 21px;
    line-height: 24px;
    color: var(--title-grey);
  }

  .feature-body {
    margin-top: 10px;
    font-family: "Noto Sans", sans-serif;
    font-size: 13px;
    line-height: 20px;
    color: var(--body-grey);
  }

  .feature-link {
    display: block;
    margin-top: 9px;
    font-family: "Noto Serif", serif;
    font-style: italic;
    font-size: 15px;
    color: var(--link-green);
    text-decoration: none;
  }
</style>
</head>
<body>
<div class="page">

  <header class="masthead" role="img" aria-label="Backdrop of translucent green and turquoise leaf skeletons">
    <div class="portrait" role="img" aria-label="Portrait photo of Carla Whitford smiling outdoors"></div>

    <div class="brand">
      <span class="brand-dot"></span>
      <span class="brand-name">Bright Meadow<br>Table</span>
    </div>

    <div class="signature">Carla Whitford</div>

    <section class="optin">
      <p class="optin-lead">SIGN UP to receive Carla's monthly newsletter and receive here...</p>
      <p class="optin-offer">Complimentary Pantry<br>Basket Planner!</p>
      <div class="optin-form">
        <span class="field">First Name</span>
        <span class="field">Last Name</span>
        <span class="field">Email</span>
        <span class="signup-button">SIGN UP</span>
      </div>
    </section>
  </header>

  <nav class="main-nav">
    <span class="nav-item is-current">Home</span>
    <span class="nav-item">Speaking&nbsp;»</span>
    <span class="nav-item">Counseling&nbsp;»</span>
    <span class="nav-item">Retreats &amp; Classes</span>
    <span class="nav-item">Meet Carla&nbsp;»</span>
    <span class="nav-item">Store&nbsp;»</span>
    <span class="nav-item">Blog</span>
    <span class="nav-item">References</span>
    <span class="nav-item">Media</span>
  </nav>

  <main class="features">
    <article class="feature">
      <div class="feature-image speaker" role="img" aria-label="Photo of Carla speaking on stage"></div>
      <div class="feature-text">
        <h2 class="feature-title">Motivational Speaker</h2>
        <p class="feature-body">Carla is a member of the Regional Speakers Guild, traveling internationally, employee wellness programs and ...</p>
        <a class="feature-link" href="#">Learn more</a>
      </div>
    </article>

    <article class="feature">
      <div class="feature-image counseling" role="img" aria-label="Framed snapshot of Carla with a microphone"></div>
      <div class="feature-text">
        <h2 class="feature-title">Nutrition Counseling</h2>
        <p class="feature-body">Whether you are looking for individualized personal health &amp; nutrition counseling, family coaching, cooking classes or a private...</p>
        <a class="feature-link" href="#">Learn more</a>
      </div>
    </article>

    <article class="feature">
      <div class="feature-image products" role="img" aria-label="Stack of Carla's nutrition books and DVDs"></div>
      <div class="feature-text">
        <h2 class="feature-title">Best Nutrition, Books &amp; Products</h2>
        <p class="feature-body">Books &amp; DVD’s on nutrition &amp; healthy recipes. Food, Body Care, &amp; Home Products. Find it all here.</p>
        <a class="feature-link" href="#">Learn more</a>
      </div>
    </article>
  </main>

</div>
</body>
</html>
```